Real Estate Company Looking for Business Card Designs for 3 Executives

Hello!
Thanks so much for considering our project! We are a real estate investment company located in Edmonton, Alberta called Bellhaven Group of Companies. We invest/develop both commercial and residential real estate and are looking to create 3 DOUBLE-SIDED business cards for 3 top executives in the company! (for some reason it won't let us select the double-sided option, but yes, the cards are double sided and would be happy to tip extra)

We have certain guidelines that we want our business cards to for sure follow - the back of the Business card has to be the Black Background Version of the Logo which has already been designed and linked as a file (first file). We want the entire back of the card to simply just be the black background logo. In terms of the front of the card, would like to see a smaller version of the white background logo (linked as the second file) in the top left hand corner - of course, feel free to get creative and we can make revisions together along the way! and Then after that, just text. We want the card to be sharp, clean, easy on the eyes and highly professional looking. We would like the card to include the Full name of the Company (Bellhaven Group of Companies), Name of the Person, Title, Phone, Email. If possible please provide the front part of the card for 3 people:

1) Bellhaven Group of Companies, Liora Quenby, Chief Financial Officer, 780-555-0142, lioraquenby@bellhavengroup.example

2) Bellhaven Group of Companies, Tobias Quenby, Chief Executive Officer, 780-555-0187, tobiasquenby@bellhavengroup.example

3) Bellhaven Group of Companies, Rui Delcourt, Chief Operations Officer, 587-555-0163, ruidelcourt@bellhavengroup.example

Thank you so much for considering our project & we look forward to seeing your designs!

```html
<!DOCTYPE html>
<html lang="en">
<head>
<meta charset="UTF-8">
<title>Bellhaven Group of Companies – Business Cards</title>
<link href="https://fonts.googleapis.com/css2?family=Work+Sans:wght@400;600&display=swap" rel="stylesheet">
<style>
  :root {
    --backdrop: #d6d6d6;
    --card: #262626;
    --card-deep: #1d1d1d;
    --ink-strong: #d9d9d9;
    --ink-soft: #b4b4b4;
    --ink-muted: #8a8a8a;
  }
  * { margin: 0; padding: 0; box-sizing: border-box; }
  html, body {
    width: 1200px;
    height: 800px;
    overflow: hidden;
  }
  body {
    background: var(--backdrop);
    font-family: "Work Sans", Arial, sans-serif;
    display: grid;
    grid-template-columns: 540px 540px;
    grid-template-rows: 309px 309px;
    gap: 40px;
    justify-content: center;
    align-content: center;
  }
  .card {
    width: 540px;
    height: 309px;
    border-radius: 18px;
    background: var(--card);
    position: relative;
    overflow: hidden;
  }

  /* Front */
  .forest-artwork {
    position: absolute;
    left: 0;
    top: 0;
    width: 170px;
    height: 100%;
    background: linear-gradient(90deg, var(--card-deep) 0%, #4a4a4a 35%, #8c8c8c 60%, #3c3c3c 100%);
  }
  .front-lockup {
    position: absolute;
    left: 196px;
    top: 30px;
    display: flex;
    align-items: center;
    gap: 10px;
  }
  .front-lockup .brand-mark {
    width: 12px;
    height: 12px;
    background: var(--ink-soft);
  }
  .front-lockup .brand-name {
    font-size: 13px;
    font-weight: 400;
    letter-spacing: 0.4em;
    color: var(--ink-soft);
    text-transform: uppercase;
  }
  .contact-block {
    position: absolute;
    right: 36px;
    top: 84px;
    text-align: right;
  }
  .person-name {
    font-weight: 600;
    font-size: 20px;
    letter-spacing: 0.06em;
    color: var(--ink-strong);
    text-transform: uppercase;
    line-height: 1.1;
  }
  .person-title {
    font-size: 12px;
    color: var(--ink-soft);
    margin-top: 4px;
    line-height: 1.35;
  }
  .company-name {
    font-size: 12px;
    color: var(--ink-muted);
    line-height: 1.35;
  }
  .contact-list {
    list-style: none;
    margin-top: 18px;
  }
  .contact-list li {
    display: flex;
    justify-content: flex-end;
    align-items: center;
    gap: 10px;
    font-size: 12px;
    color: var(--ink-soft);
    line-height: 1.6;
    white-space: nowrap;
  }
  .contact-icon {
    width: 12px;
    height: 12px;
    flex: none;
  }

  /* Back */
  .card-back {
    background: var(--card-deep);
    display: flex;
    align-items: center;
    justify-content: center;
  }
  .back-lockup {
    display: flex;
    align-items: center;
    gap: 16px;
  }
  .back-lockup .brand-mark {
    width: 22px;
    height: 22px;
    background: var(--ink-muted);
  }
  .back-lockup .brand-name {
    font-weight: 400;
    font-size: 26px;
    letter-spacing: 0.45em;
    color: var(--ink-muted);
    text-transform: uppercase;
  }
</style>
</head>
<body>

  <section class="card card-front">
    <div class="forest-artwork" role="img" aria-label="Glossy spot-varnish forest illustration of tall trees"></div>
    <div class="front-lockup"><span class="brand-mark" aria-hidden="true"></span><span class="brand-name">Bellhaven</span></div>
    <div class="contact-block">
      <h1 class="person-name">Liora Quenby</h1>
      <p class="person-title">Chief Financial Officer</p>
      <p class="company-name">Bellhaven Group of Companies</p>
      <ul class="contact-list">
        <li>780-555-0142
          <svg class="contact-icon" viewBox="0 0 12 12" aria-hidden="true"><path d="M3 1.5 L4.6 3.6 L3.7 4.6 Q5 7 7.4 8.3 L8.4 7.4 L10.5 9 L9.4 10.5 Q4.5 10 1.5 2.6 Z" fill="#b4b4b4"/></svg>
        </li>
        <li>lioraquenby@bellhavengroup.example
          <svg class="contact-icon" viewBox="0 0 12 12" aria-hidden="true"><rect x="1" y="2.5" width="10" height="7" rx="1" fill="#b4b4b4"/><path d="M1.5 3 L6 6.5 L10.5 3" stroke="#262626" stroke-width="1" fill="none"/></svg>
        </li>
        <li>bellhavengroup.example
          <svg class="contact-icon" viewBox="0 0 12 12" aria-hidden="true"><circle cx="6" cy="6" r="5" fill="#b4b4b4"/><path d="M1 6 H11 M6 1 Q3 6 6 11 M6 1 Q9 6 6 11" stroke="#262626" stroke-width="0.8" fill="none"/></svg>
        </li>
      </ul>
    </div>
  </section>

  <section class="card card-front">
    <div class="forest-artwork" role="img" aria-label="Glossy spot-varnish forest illustration of tall trees"></div>
    <div class="front-lockup"><span class="brand-mark" aria-hidden="true"></span><span class="brand-name">Bellhaven</span></div>
    <div class="contact-block">
      <h1 class="person-name">Tobias Quenby</h1>
      <p class="person-title">Chief Executive Officer</p>
      <p class="company-name">Bellhaven Group of Companies</p>
      <ul class="contact-list">
        <li>780-555-0187
          <svg class="contact-icon" viewBox="0 0 12 12" aria-hidden="true"><path d="M3 1.5 L4.6 3.6 L3.7 4.6 Q5 7 7.4 8.3 L8.4 7.4 L10.5 9 L9.4 10.5 Q4.5 10 1.5 2.6 Z" fill="#b4b4b4"/></svg>
        </li>
        <li>tobiasquenby@bellhavengroup.example
          <svg class="contact-icon" viewBox="0 0 12 12" aria-hidden="true"><rect x="1" y="2.5" width="10" height="7" rx="1" fill="#b4b4b4"/><path d="M1.5 3 L6 6.5 L10.5 3" stroke="#262626" stroke-width="1" fill="none"/></svg>
        </li>
        <li>bellhavengroup.example
          <svg class="contact-icon" viewBox="0 0 12 12" aria-hidden="true"><circle cx="6" cy="6" r="5" fill="#b4b4b4"/><path d="M1 6 H11 M6 1 Q3 6 6 11 M6 1 Q9 6 6 11" stroke="#262626" stroke-width="0.8" fill="none"/></svg>
        </li>
      </ul>
    </div>
  </section>

  <section class="card card-front">
    <div class="forest-artwork" role="img" aria-label="Glossy spot-varnish forest illustration of tall trees"></div>
    <div class="front-lockup"><span class="brand-mark" aria-hidden="true"></span><span class="brand-name">Bellhaven</span></div>
    <div class="contact-block">
      <h1 class="person-name">Rui Delcourt</h1>
      <p class="person-title">Chief Operations Officer</p>
      <p class="company-name">Bellhaven Group of Companies</p>
      <ul class="contact-list">
        <li>587-555-0163
          <svg class="contact-icon" viewBox="0 0 12 12" aria-hidden="true"><path d="M3 1.5 L4.6 3.6 L3.7 4.6 Q5 7 7.4 8.3 L8.4 7.4 L10.5 9 L9.4 10.5 Q4.5 10 1.5 2.6 Z" fill="#b4b4b4"/></svg>
        </li>
        <li>ruidelcourt@bellhavengroup.example
          <svg class="contact-icon" viewBox="0 0 12 12" aria-hidden="true"><rect x="1" y="2.5" width="10" height="7" rx="1" fill="#b4b4b4"/><path d="M1.5 3 L6 6.5 L10.5 3" stroke="#262626" stroke-width="1" fill="none"/></svg>
        </li>
        <li>bellhavengroup.example
          <svg class="contact-icon" viewBox="0 0 12 12" aria-hidden="true"><circle cx="6" cy="6" r="5" fill="#b4b4b4"/><path d="M1 6 H11 M6 1 Q3 6 6 11 M6 1 Q9 6 6 11" stroke="#262626" stroke-width="0.8" fill="none"/></svg>
        </li>
      </ul>
    </div>
  </section>

  <section class="card card-back">
    <div class="back-lockup">
      <span class="brand-mark" aria-hidden="true"></span>
      <span class="brand-name">Bellhaven</span>
    </div>
  </section>

</body>
</html>
```